Ferrow Hip Hop Dance Theater Flyer

Ferrow is a hip-hop dance theater company based in Los Angeles under the artistic direction of Lena “Reedowl” Marbury. Ferrow creates multimedia urban dance performances that incorporate street dance, poetry, theater, and film into provocative and daring performances. Speaking the language of Hip-Hop, Ferrow tells stories using the movement vocabulary of street dance styles including: bboying/bgirling, krump dance, house dance, locking, popping, waacking, and capoeira. Founded in 2007, Ferrow dancers represent the best in LA with extensive credits that include major films, TV shows, and music videos. Ferrow is committed to innovating the realm of hip-hop dance theater as well as uplifting the community through residencies, workshops, and special events.
Target Market(s)
Presenters- theater managers who might book our performances, event producers, middle and upper class parents who might hire Ferrow to perform at private events
Industry/Entity Type
Performing Art
Requirements
Must have
- Text/Copy as describe in word .doc "Ferrow General Flyer Copy"
- One main featured photo of multiple dancers with 2-3 secondary photos of single dancers and/or small groups of dancers.
- Clean, not-too-busy design
- Easy to read text
Nice to have
- A design similar in feel and layout to the "Old Ferrow Flyer" that's included for reference
- Use of bright neon green as an accent color
Should not have
- Lots of manipulation of the photographs

```html
<!DOCTYPE html>
<html lang="en">
<head>
<meta charset="utf-8">
<title>Ferrow Hip Hop Dance Theater Flyer</title>
<link rel="stylesheet" href="https://fonts.googleapis.com/css2?family=Arimo:ital,wght@0,400;0,700;1,400&display=swap">
<style>
  :root {
    --stage-black: #0b0707;
    --stage-red: #6e1a14;
    --stage-glow: #a8392a;
    --panel-green: #7fa52a;
    --panel-green-light: #a9c64a;
    --panel-green-dark: #4f6f1c;
    --band-green: #3f5916;
    --text-white: #ffffff;
  }
  * { margin: 0; padding: 0; box-sizing: border-box; }
  html, body {
    width: 1200px;
    height: 789px;
    overflow: hidden;
    background: var(--stage-black);
  }
  .flyer {
    position: relative;
    width: 1200px;
    height: 789px;
    overflow: hidden;
    font-family: "Arimo", Arial, sans-serif;
    color: var(--text-white);
  }
  .feature-photo {
    position: absolute;
    left: 0;
    top: 0;
    width: 657px;
    height: 789px;
    background:
      radial-gradient(ellipse 60% 45% at 45% 62%, var(--stage-glow) 0%, rgba(110,26,20,0.55) 45%, transparent 80%),
      linear-gradient(180deg, var(--stage-black) 0%, #1a0b09 55%, var(--stage-red) 85%, #2a0c08 100%);
  }
  .info-panel {
    position: absolute;
    left: 657px;
    top: 0;
    width: 543px;
    height: 789px;
    background:
      radial-gradient(ellipse 45% 55% at 55% 45%, rgba(190,215,110,0.45) 0%, transparent 75%),
      linear-gradient(180deg, var(--panel-green) 0%, var(--panel-green-light) 40%, var(--panel-green) 70%, var(--panel-green-dark) 100%);
    text-align: center;
  }
  .wordmark {
    position: absolute;
    top: 90px;
    left: 0;
    width: 100%;
    font-size: 112px;
    font-weight: 700;
    letter-spacing: 2px;
    line-height: 1;
  }
  .headline {
    position: absolute;
    top: 299px;
    left: 0;
    width: 100%;
    font-size: 26px;
    line-height: 30px;
    font-weight: 700;
    text-shadow: 0 1px 2px rgba(0,0,0,0.35);
  }
  .reviews { list-style: none; }
  .review {
    position: absolute;
    left: 14px;
    width: 515px;
    font-size: 18.5px;
    line-height: 24.5px;
    text-shadow: 0 1px 2px rgba(0,0,0,0.3);
  }
  .review--first { top: 331px; padding: 0 40px; }
  .review--second { top: 453px; }
  .review--third { top: 617px; }
  .review-quote { font-style: italic; }
  .review-source { display: block; }
  .site-band {
    position: absolute;
    left: 657px;
    top: 753px;
    width: 543px;
    height: 36px;
    background: var(--band-green);
    font-size: 20px;
    line-height: 36px;
    text-align: center;
  }
</style>
</head>
<body>
<main class="flyer">
  <div class="feature-photo" role="img" aria-label="Stage photo of five hip-hop dancers in black company T-shirts posing together under red stage light"></div>

  <section class="info-panel">
    <div class="wordmark">Ferrow</div>
    <h1 class="headline">Multimedia hip-hop dance theater</h1>
    <ul class="reviews">
      <li class="review review--first">
        <span class="review-quote">“Reclaiming hip-hop… by expanding the idiom’s creative horizons…”</span>
        <span class="review-source">-Pacific Coast Herald</span>
      </li>
      <li class="review review--second">
        <span class="review-quote">“The thrilling group choreography… suggested solidarity in the streets, a sense that the b-boy/b-girl community itself lifts its members toward loftier horizons even as they contort their bodies upside down.”</span>
        <span class="review-source">-Stage Motion Review</span>
      </li>
      <li class="review review--third">
        <span class="review-quote">“The vision for ancient myths has been owned for decades by the fearless Ada Whitcombe… Yet Marbury, seized a piece of that sacred territory with the debut of ‘Lanterns of the Deep.’”</span>
        <span class="review-source">-Pacific Coast Herald</span>
      </li>
    </ul>
  </section>

  <footer class="site-band">ferrowperformance.com</footer>
</main>
</body>
</html>
```